Webdesign für Zahnarztpraxis
Zielgruppe
Zahnarztpraxis
Aufgabenstellung
- Klares und übersichtliches Desgin
- Nicht zu verspielt
- Informativ
- Leichte Naviagtion
- Das Design der alten Webseite soll NICHT kopiert werden
- Die Farben Blau und Grün aus dem Logo sollen sich wiederfinden
- Designbeispiele, die dem Kunden gefallen sind https://www.falkmann-ostrup-zahnarztpraxis.de/ und https://www.zahvilkorn.de/

```html
<!DOCTYPE html>
<html lang="de">
<head>
<meta charset="utf-8">
<title>Dentalpraxis &amp; Labor Marta Kessling</title>
<link href="https://fonts.googleapis.com/css2?family=Inter:wght@400;500;600;700&display=swap" rel="stylesheet">
<style>
:root{
  --blue:#3b82f0;
  --green:#6cb33f;
  --mint:#f4f8ec;
  --text:#1f2430;
  --muted:#4a4f5a;
  --white:#ffffff;
}
*{box-sizing:border-box;margin:0;padding:0}
html,body{width:1200px;height:3382px;overflow:hidden}
body{font-family:"Inter",sans-serif;color:var(--text);background:var(--white);font-size:13px;line-height:1.6}
.wrap{width:946px;margin:0 auto;position:relative}
a{color:inherit;text-decoration:none}

.topbar{height:37px;background:var(--mint);font-size:12px}
.topbar .wrap{display:flex;justify-content:space-between;align-items:center;height:37px}
.topbar .item{display:flex;align-items:center;gap:8px}
.topbar .right{display:flex;align-items:center;gap:18px}
.topbar .sep{width:1px;height:14px;background:var(--text)}

.nav{height:84px;background:var(--white)}
.nav .wrap{display:flex;justify-content:space-between;align-items:center;height:84px}
.brand{display:flex;align-items:center;gap:10px;font-size:22px;font-weight:600;color:var(--blue)}
.brand .dot{width:26px;height:26px;border-radius:50%;background:var(--green)}
.menu{display:flex;gap:26px;font-size:14px}
.menu .active{color:var(--blue);font-weight:600}

.hero{height:458px;position:relative;background:linear-gradient(100deg,#c9b6ae 0%,#e9d4cc 40%,#c98a86 70%,#e8c5bf 100%)}
.hero-box{position:absolute;left:129px;top:108px;width:383px;height:180px;background:var(--blue);color:var(--white);padding:16px 17px}
.hero-box h1{font-size:32px;line-height:1.17;font-weight:500;margin-bottom:10px}
.hero-box p{font-size:13px;line-height:1.7}

.notice{height:109px;background:var(--mint);font-size:13px}
.notice .wrap{padding-top:22px}
.notice u{text-decoration:underline}

.feature{position:relative;height:519px}
.feature .card{position:absolute;left:608px;top:91px;width:467px;background:rgba(255,255,255,.94);border-radius:4px;padding:24px 25px;box-shadow:0 4px 18px rgba(0,0,0,.08)}
.card h2{font-size:32px;line-height:1.17;font-weight:500;color:var(--blue);margin-bottom:16px;letter-spacing:-0.2px}
.card p{font-size:13px;line-height:1.7;color:var(--muted);margin-bottom:20px}
.btn{display:inline-block;background:var(--blue);color:var(--white);font-size:13px;font-weight:600;padding:9px 17px}
.photo-practice{background:linear-gradient(100deg,#dcdedc 0%,#b9cfcc 30%,#6fa9ad 45%,#e8eae8 65%,#a6b49a 100%)}
.photo-lab{background:linear-gradient(100deg,#d8c4b4 0%,#e7c9b6 30%,#cfc6ba 55%,#b9a690 80%,#8e7a5e 100%);height:519px}
.photo-team{background:linear-gradient(100deg,#b9b2aa 0%,#d7c2b2 35%,#eeeeee 55%,#f6f6f6 100%);height:491px}
.photo-team .card{top:98px}

.services{height:681px;background:var(--blue);color:var(--white);text-align:center;padding-top:50px}
.services h2{font-size:32px;font-weight:500;margin-bottom:54px}
.svc-row{display:flex;justify-content:center;height:130px}
.svc{width:192px;font-size:13px;font-weight:600;line-height:1.25}
.svc svg{display:block;margin:0 auto 8px;width:46px;height:46px;fill:none;stroke:var(--white);stroke-width:2;stroke-linecap:round;stroke-linejoin:round}
.services .lead{font-size:13px;line-height:1.7;margin:-4px auto 20px;width:540px}
.btn-white{display:inline-block;background:var(--white);color:var(--blue);font-weight:600;font-size:13px;padding:9px 17px}

.footer{height:484px;background:var(--mint);font-size:13px}
.footer .cols{display:flex;padding-top:40px}
.fcol1{width:384px}
.fcol2{width:260px;padding-top:10px}
.fcol3{width:302px;padding-top:10px}
.footer h3{color:var(--blue);font-size:17px;font-weight:600;margin-bottom:10px}
.footer .brand{margin-bottom:22px}
.footer dl{display:grid;grid-template-columns:86px 1fr;row-gap:2px;margin-top:10px}
.footer dt{font-weight:700}
.fcol2 .lbl{font-weight:700;margin-top:8px}
.hours{display:grid;grid-template-columns:98px 1fr;row-gap:4px;margin-bottom:8px}
.phone-hours{grid-template-columns:83px 1fr}
.legal{display:flex;gap:28px;font-size:11px;margin-top:40px}
</style>
</head>
<body>

<div class="topbar">
  <div class="wrap">
    <div class="item">
      <svg width="14" height="14" viewBox="0 0 24 24" fill="none" stroke="#1f2430" stroke-width="2"><path d="M12 22s7-6.5 7-12a7 7 0 0 0-14 0c0 5.5 7 12 7 12z"/><circle cx="12" cy="10" r="2.5"/></svg>
      Lindenweg 14, 09117 Grünhain-Altdorf
    </div>
    <div class="right">
      <div class="item"><svg width="14" height="14" viewBox="0 0 24 24" fill="none" stroke="#1f2430" stroke-width="2"><path d="M5 3h4l2 5-2.5 1.5a11 11 0 0 0 6 6L16 13l5 2v4a2 2 0 0 1-2 2A17 17 0 0 1 3 5a2 2 0 0 1 2-2z"/></svg>03721-48260</div>
      <span class="sep"></span>
      <div class="item"><svg width="14" height="14" viewBox="0 0 24 24" fill="none" stroke="#1f2430" stroke-width="2"><rect x="3" y="5" width="18" height="14" rx="1"/><path d="M3 6l9 7 9-7"/></svg>info@zahnarztpraxis-kessling.de</div>
    </div>
  </div>
</div>

<header class="nav">
  <div class="wrap">
    <div class="brand"><span class="dot"></span>Praxis Kessling</div>
    <nav class="menu">
      <a class="active" href="#">Start</a><a href="#">Praxis</a><a href="#">Eigenes Praxislabor</a><a href="#">Leistungen</a><a href="#">Unser Team</a><a href="#">Anfahrt</a>
    </nav>
  </div>
</header>

<section class="hero" role="img" aria-label="Foto: lächelnder Mund mit weißen Zähnen und Dentalspiegel">
  <div class="hero-box">
    <h1>Dentalpraxis &amp; Labor Marta Kessling</h1>
    <p>Ihre Zahnarztpraxis Kessling Grünhain-Altdorf bietet die gesamte moderne Zahnheilkunde inklusive eigenem Praxislabor.</p>
  </div>
</section>

<section class="notice">
  <div class="wrap">
    <strong>Wichtige Information für unsere Patienten:</strong><br>
    Liebe Patientinnen und Patienten, unsere Praxis ist vom 17.02. bis 24.02. und am 28.02.2025 geschlossen.<br>
    Infomieren Sie sich bitte hier über Aktualisierungen auf unserem <u>Praxis-Eintrag bei Kartenportal</u>.
  </div>
</section>

<section class="feature photo-practice" role="img" aria-label="Foto: Behandlungszimmer mit türkisem Behandlungsstuhl">
  <div class="card">
    <h2>Zahnmedizin mit eigenem Labor und Fokus auf Prävention</h2>
    <p>Ihre moderne Praxis in Grünhain-Altdorf bietet gesamte Zahnheilkunde und höchste Qualität durch das eigene Dentallabor. Unser Fokus liegt auf individueller Prävention für jedes Alter. Ihre Zahnärztin betreut Sie auf Wunsch auch fließend in Englisch.</p>
    <a class="btn" href="#">Unsere Praxis</a>
  </div>
</section>

<section class="services">
  <h2>Unser umfassendes Leistungsspektrum</h2>
  <div class="svc-row">
    <div class="svc"><svg viewBox="0 0 48 48"><circle cx="30" cy="17" r="11"/><path d="M22 25L8 39"/><path d="M26 13c2-2 6-2 8 0"/></svg>Zahnärztliche<br>Diagnostik</div>
    <div class="svc"><svg viewBox="0 0 48 48"><circle cx="22" cy="7" r="3"/><path d="M18 14v14h16v14M14 18v14h14M34 28l6 14"/></svg>Individual-<br>prophylaxe</div>
    <div class="svc"><svg viewBox="0 0 48 48"><path d="M18 42V6h14v10H24M24 16v8h6M24 24v18"/></svg>Professionelle<br>Zahnreinigung</div>
    <div class="svc"><svg viewBox="0 0 48 48"><path d="M16 10c4-2 6 0 8 1 2-1 4-3 8-1 4 3 2 12 0 16-1 3-2 6-4 6s-2-6-4-6-2 6-4 6-3-3-4-6c-2-4-4-13 0-16z"/><path d="M4 24l8 14h8M44 24l-8 14h-8"/></svg>Konservierende<br>Zahnheilkunde</div>
    <div class="svc"><svg viewBox="0 0 48 48"><rect x="14" y="6" width="20" height="10" rx="5"/><path d="M24 16v8M14 30h20M10 42l4-12M38 42l-4-12M8 42h32"/></svg>Zahnärztliche<br>Prothetik</div>
  </div>
  <div class="svc-row">
    <div class="svc"><svg viewBox="0 0 48 48"><path d="M6 10h36v8c0 12-8 20-18 20S6 30 6 18z"/><path d="M12 10v10M18 10v12M24 10v12M30 10v12M36 10v10M10 22h28"/></svg>Kiefer-<br>orthopädie</div>
    <div class="svc"><svg viewBox="0 0 48 48"><path d="M6 40h36M10 40V28h10v12M20 34h14l4-10M30 8l6 6M36 8l-10 14"/><circle cx="15" cy="22" r="3"/></svg>Chirurgische<br>Zahnheilkunde</div>
    <div class="svc"><svg viewBox="0 0 48 48"><path d="M14 10c5-3 7 0 10 1 3-1 5-4 10-1 5 4 2 14 0 19-1 4-2 9-5 9s-3-8-5-8-2 8-5 8-4-5-5-9c-2-5-5-15 0-19z"/><path d="M36 4v6M33 7h6"/></svg>Ästhetische<br>Zahnheilkunde</div>
    <div class="svc"><svg viewBox="0 0 48 48"><path d="M6 14V6h8M34 6h8v8M42 34v8h-8M14 42H6v-8"/><path d="M16 14c4-2 6 0 8 1 2-1 4-3 8-1 4 3 2 11 0 14-1 3-2 7-4 7s-2-6-4-6-2 6-4 6-3-4-4-7c-2-3-4-11 0-14z"/></svg>Ganzheitliche<br>Zahnheilkunde</div>
  </div>
  <div class="svc-row">
    <div class="svc"><svg viewBox="0 0 48 48"><path d="M17 16c3-2 5 0 7 1 2-1 4-3 7-1 3 2 2 9 0 12-1 3-2 6-3.5 6S26 30 24 30s-2 4-3.5 4S18 31 17 28c-2-3-3-10 0-12z"/><path d="M8 10l2 4M40 10l-2 4M24 4v5M10 40h28"/></svg>Kinderzahn-<br>heilkunde</div>
    <div class="svc"><svg viewBox="0 0 48 48"><path d="M6 8h36v10c0 12-8 20-18 20S6 30 6 18z"/><path d="M12 8v10M18 8v12M24 8v12M30 8v12M36 8v10M10 20h28M18 30h12"/></svg>Bioverträglicher<br>Zahnersatz</div>
  </div>
  <p class="lead">Von Diagnostik und Prophylaxe bis zu Prothetik und Chirurgie: Wir bieten Ihnen das komplette Spektrum der modernen Zahnheilkunde.</p>
  <a class="btn-white" href="#">Leistungen</a>
</section>

<section class="feature photo-lab" role="img" aria-label="Foto: Zahntechnikerin im Praxislabor an einem Arbeitsplatz">
  <div class="card">
    <h2>Höchste Qualität, schnelle Ergebnisse: Unser eigenes Praxislabor</h2>
    <p>Kurze Wege und präzise Ergebnisse: Unsere Praxis verfügt über ein eigenes Dentallabor. Das sichert Ihnen bioverträglichen Zahnersatz und höchste Individualität direkt vor Ort.</p>
    <a class="btn" href="#">Eigenes Praxislabor</a>
  </div>
</section>

<section class="feature photo-team" role="img" aria-label="Foto: fünf Mitarbeiterinnen des Praxisteams vor heller Wand">
  <div class="card">
    <h2>Ihr Team für gesunde Zähne: Kompetent und immer für Sie da.</h2>
    <p>Lernen Sie uns kennen: Unser kompetentes und herzliches Praxisteam ist darauf fokussiert, Sie in allen Fragen der Zahngesundheit optimal zu unterstützen.</p>
    <a class="btn" href="#">Unser Team</a>
  </div>
</section>

<footer class="footer">
  <div class="wrap">
    <div class="cols">
      <div class="fcol1">
        <div class="brand"><span class="dot"></span>Praxis Kessling</div>
        <p>Unsere Praxis bleibt in folgenden Zeiträumen<br>wegen Praxisurlaub geschlossen:</p>
        <dl><dt>Winter</dt><dd>17.02.2025 – 24.02.2025</dd><dt>Schließtag</dt><dd>28.02.2025</dd></dl>
      </div>
      <div class="fcol2">
        <h3>So erreichen Sie uns</h3>
        <p class="lbl">Adresse</p><p>Lindenweg 14<br>09117 Grünhain-Altdorf</p>
        <p class="lbl">Telefon</p><p>03721-48260</p>
        <p class="lbl">Fax</p><p>03721-48261</p>
        <p class="lbl">E-Mail</p><p>info@zahnarztpraxis-kessling.de</p>
      </div>
      <div class="fcol3">
        <h3>Öffnungszeiten</h3>
        <dl class="hours">
          <dt>Montag:</dt><dd>9:00 - 13:00 &amp; 14:00 - 19:00 Uhr</dd>
          <dt>Dienstag</dt><dd>9:00 - 13:00 &amp; 14:00 - 19:00 Uhr</dd>
          <dt>Mittwoch</dt><dd>9:00 - 14:00 Uhr</dd>
          <dt>Donnerstag</dt><dd>geschlossen</dd>
          <dt>Freitag</dt><dd>9:00 - 13:00 Uhr</dd>
        </dl>
        <p style="margin-bottom:20px">... und nach Vereinbarung</p>
        <h3>Telefonzeiten</h3>
        <p style="margin-bottom:10px">Innerhalb dieser Zeiten sind wir für<br>Sie telefonisch erreichbar:</p>
        <dl class="hours phone-hours">
          <dt>Montag:</dt><dd>9:00 - 15:00 Uhr</dd>
          <dt>Dienstag</dt><dd>9:00 - 15:00 Uhr</dd>
          <dt>Mittwoch</dt><dd>9:00 - 12:00 Uhr</dd>
        </dl>
      </div>
    </div>
    <div class="legal"><span>Copyright ©2025</span><a href="#">Impressum</a><a href="#">Datenschutz</a><a href="#">Cookie-Einstellungen</a></div>
  </div>
</footer>

</body>
</html>
```